Brenwick Structures Construction Company Seeking Modern Website

We are a small construction company wanting to create a web presence. We don't have much in the way of current content but will get photos as they come in. Attached is a picture of our business card.
The pages we would like on the menu are:
Home
Portfolio
Product Specs
Testimonials
Our Process
Contact
Some designs we like are:
http://www.tovasheds-example.com/
http://www.qrnstructures-example.com/
http://dunholtbarns-example.com/
http://pellingframes-example.com/
Not much requirements other than that so feel free to be creative!
Updates
Target Market(s)
Construction
Commercial and Residential Buildings
Industry/Entity Type
Construction Company
Number of Pages Required
5+ page
Look and feel

```html
<!DOCTYPE html>
<html lang="en">
<head>
<meta charset="utf-8">
<title>Brenwick Structures</title>
<link href="https://fonts.googleapis.com/css2?family=Roboto:wght@400;500;700&family=Source+Sans+3:ital,wght@0,400;0,600;1,400&family=PT+Sans:wght@700&display=swap" rel="stylesheet">
<style>
:root{
  --red:#d7281e;
  --red-soft:rgba(215,40,30,.82);
  --ink:#333;
  --grey:#6f6f6f;
  --light:#efefef;
  --band:#ececec;
  --line:#d6d6d6;
  --blue:#1a9ad6;
}
*{margin:0;padding:0;box-sizing:border-box}
html,body{width:1018px;height:1200px;overflow:hidden;background:#fff}
body{position:relative;font-family:"Source Sans 3",Arial,sans-serif;color:var(--ink)}
.abs{position:absolute}
.topline{left:0;top:0;width:1018px;height:2px;background:#333}
.brand{left:50px;top:40px;font-family:"Roboto",sans-serif;font-weight:700;font-size:27px;color:var(--red);display:flex;align-items:center;gap:9px}
.brand-dot{width:18px;height:18px;border-radius:50%;background:var(--red)}
.utility{right:50px;top:30px;display:flex;align-items:center;font-family:"Roboto",sans-serif;font-size:13px;color:#888}
.utility a{color:#888;text-decoration:none;padding:0 13px;border-right:1px solid #ccc;line-height:13px}
.utility a.active{color:var(--red)}
.utility .call{padding-left:11px}
.utility .phone{color:#222;font-size:15px;margin-left:7px;margin-right:10px}
.mainnav{right:50px;top:66px;display:flex;gap:36px;font-family:"Roboto",sans-serif;font-size:14px}
.mainnav a{color:#333;text-decoration:none}
.mainnav a.active{color:var(--red)}
.hero{left:0;top:110px;width:1018px;height:410px}
.caption{left:18px;top:390px;width:418px;height:88px;border-radius:50%;background:var(--red-soft);color:#fff;font-family:"PT Sans",sans-serif;font-weight:700;font-size:18px;line-height:25px;text-align:center;padding-top:21px;padding-left:20px}
.dots{display:flex;gap:5px}
.dots span{width:10px;height:10px;border-radius:50%;border:1.5px solid #fff}
.dots span.on{background:#fff}
.services{left:0;top:520px;width:1018px;height:125px;background:var(--band)}
.service-divider{left:509px;top:520px;width:1px;height:125px;background:var(--line)}
.service h2{font-weight:400;font-size:19px;color:var(--red);margin-bottom:10px}
.service p{font-size:12px;line-height:20px;color:var(--grey)}
.service.left{left:90px;top:544px;width:295px;text-align:right}
.service.right{left:634px;top:544px;width:300px}
.icon-ring{width:70px;height:70px;border-radius:50%;border:1px solid var(--red)}
.welcome{left:100px;top:690px;width:818px;text-align:center}
.welcome h1{font-weight:400;font-size:23px;color:var(--red);margin-bottom:16px}
.welcome p{font-size:12px;line-height:23.5px;color:var(--grey)}
.soft-rule{left:180px;top:840px;width:660px;height:4px;background:radial-gradient(ellipse at center,#e6e6e6 0%,rgba(255,255,255,0) 70%)}
.avatar{left:107px;top:889px;width:72px;height:72px;border-radius:50%;background:linear-gradient(160deg,#e8c690,#b08a5e);border:2px solid #fff;box-shadow:0 0 0 1px #888}
.quote-text{left:288px;top:900px;width:640px;font-style:italic;font-size:12px;line-height:23.5px;color:var(--grey)}
.quote-name{left:287px;top:950px;font-style:italic;font-size:15px;color:var(--red)}
.dots.blue{left:855px;top:954px}
.dots.blue span{border-color:#333}
.dots.blue span.on{background:var(--blue);border-color:var(--blue)}
.footer{left:0;top:1020px;width:1018px;height:180px;background:var(--light);border-top:2px solid #ddd}
.col-rule{top:1045px;width:1px;height:132px;background:var(--line)}
footer h3{font-weight:400;font-size:19px;color:var(--red)}
.social{left:67px;top:1083px;display:grid;grid-template-columns:21px 21px;gap:7px 7px}
.social span{width:21px;height:21px;border-radius:50%}
.contact{left:152px;top:1081px;width:195px;font-size:12px}
.contact .label{font-size:12px;color:#222;margin-bottom:8px}
.contact .row{display:flex;align-items:center;gap:10px;font-size:14px;color:#555;margin-bottom:7px;white-space:nowrap}
.contact .row.tel{font-family:"Roboto",sans-serif;font-size:15px;color:#222}
.small{font-size:11px;line-height:18px;color:var(--grey)}
.zip{left:382px;top:1120px;width:166px;height:29px;background:#fff;border:1px solid #ccc;border-radius:2px;font-size:9px;color:#aaa;padding:8px 8px}
.locate{left:555px;top:1120px;width:81px;height:29px;background:var(--blue);color:#fff;font-size:12px;font-weight:600;text-align:center;line-height:29px}
.news-title{font-size:12px;color:#222;font-weight:600;text-transform:uppercase}
.readmore{font-style:italic;font-size:12px;color:var(--blue)}
</style>
</head>
<body>
<div class="abs topline"></div>

<header>
  <div class="abs brand"><span class="brand-dot"></span>Brenwick Structures</div>
  <nav class="abs utility">
    <a href="#">Location</a><a href="#">FAQ's</a><a href="#" class="active">Contact us</a>
    <span class="call">Call us Today</span><span class="phone">0147 258 369</span>
    <svg width="10" height="17" viewBox="0 0 10 17"><rect x="1" y="1" width="8" height="15" rx="1.5" fill="none" stroke="#d7281e" stroke-width="1.6"/><circle cx="5" cy="13" r="1" fill="#d7281e"/></svg>
  </nav>
  <nav class="abs mainnav">
    <a href="#" class="active">Home</a><a href="#">Portfolio</a><a href="#">Product Specs</a><a href="#">Testimonials</a><a href="#">Our Process</a><a href="#">Contact</a>
  </nav>
</header>

<section>
  <svg class="abs hero" viewBox="0 0 1018 410" role="img" aria-label="Photo of a brown wooden building with a bell tower on open prairie under a blue sky">
    <defs>
      <linearGradient id="sky" x1="0" y1="0" x2="0" y2="1">
        <stop offset="0" stop-color="#4f7ec4"/>
        <stop offset=".55" stop-color="#a9c3e4"/>
        <stop offset=".74" stop-color="#c9b890"/>
        <stop offset="1" stop-color="#a98f5c"/>
      </linearGradient>
    </defs>
    <path d="M0 14 Q509 -12 1018 14 V410 H0 Z" fill="url(#sky)"/>
    <path d="M0 14 Q509 -12 1018 14" fill="none" stroke="#222" stroke-width="1.5"/>
  </svg>
  <div class="abs caption">We Provide Commercial Construction<br>and Residential Buildings.</div>
  <div class="abs dots" style="left:489px;top:492px"><span></span><span class="on"></span><span></span></div>
</section>

<section>
  <div class="abs services"></div>
  <div class="abs service-divider"></div>
  <div class="abs service left">
    <h2>Commercial Construction</h2>
    <p>Lorem ipsum dolor sit amet, consectetur adipiscing elit do .eiusmod tempor incididunt ut labore aliqua</p>
  </div>
  <div class="abs icon-ring" style="left:409px;top:549px">
    <svg width="70" height="70" viewBox="0 0 70 70"><rect x="24" y="20" width="22" height="30" fill="none" stroke="#d7281e" stroke-width="3"/><g fill="#d7281e"><rect x="29" y="25" width="4" height="4"/><rect x="37" y="25" width="4" height="4"/><rect x="29" y="32" width="4" height="4"/><rect x="37" y="32" width="4" height="4"/><rect x="29" y="39" width="4" height="4"/><rect x="37" y="39" width="4" height="4"/></g></svg>
  </div>
  <div class="abs icon-ring" style="left:536px;top:549px">
    <svg width="70" height="70" viewBox="0 0 70 70"><path d="M35 21 L50 35 H46 V48 H39 V40 H31 V48 H24 V35 H20 Z" fill="#d7281e"/></svg>
  </div>
  <div class="abs service right">
    <h2>Residential Buildings</h2>
    <p>Lorem ipsum dolor sit amet, consectetur adipiscing elit do eiusmod tempor incididunt ut labore aliqua.</p>
  </div>
</section>

<section class="abs welcome">
  <h1>Welcome to Brenwick Structures</h1>
  <p>Lorem ipsum dolor sit amet, consectetur adipiscing elit, sed do eiusmod tempor incididunt ut labore et dolore magna aliqua.. Duis aute irure dolor in reprehenderit in voluptate velit esse cillum dolore eu fugiat nulla pariatur. Excepteur sint occaecat cupidatat non proident sunt ut enim ad minim veniam, quis nostrud exercitation ullamco laboris nisi ut aliquip ex ea&nbsp; aute irure dolor in reprehenderit in voluptate velit esse&nbsp; commodo consequat.</p>
</section>
<div class="abs soft-rule"></div>

<section>
  <div class="abs avatar" role="img" aria-label="Portrait photo of the client"></div>
  <svg class="abs" style="left:190px;top:878px" width="90" height="95" viewBox="0 0 90 95">
    <path d="M22 4 Q12 4 12 16 V38 Q12 46 4 47 Q12 48 12 56 V80 Q12 92 22 92" fill="none" stroke="#666" stroke-width="4"/>
    <g fill="#c8c8c8"><circle cx="46" cy="24" r="9"/><path d="M38 24 Q38 8 52 4 L53 7 Q44 12 44 20 Z"/><circle cx="70" cy="24" r="9"/><path d="M62 24 Q62 8 76 4 L77 7 Q68 12 68 20 Z"/></g>
  </svg>
  <p class="abs quote-text">Lorem ipsum dolor sit amet, consectetur adipiscing elit, sed do eiusmod tempor incididunt ut labore et dolore magna aliqua.<br>Duis aute irure dolor in reprehenderit in voluptate velit esse cillum dolore eu fugiat nulla pariatur.</p>
  <div class="abs quote-name">Marla Quenby</div>
  <div class="abs dots blue"><span></span><span class="on"></span><span></span></div>
</section>

<footer>
  <div class="abs footer"></div>
  <div class="abs col-rule" style="left:354px"></div>
  <div class="abs col-rule" style="left:660px"></div>

  <h3 class="abs" style="left:67px;top:1041px">Keep in Touch</h3>
  <div class="abs social">
    <span style="background:#2a5ea8"></span><span style="background:#35a4d6"></span>
    <span style="background:#d04a3a"></span><span style="background:#c8232c"></span>
    <span style="background:#2b4c8c"></span><span style="background:#f29a25"></span>
  </div>
  <div class="abs" style="left:132px;top:1083px;width:1px;height:64px;background:var(--line)"></div>
  <div class="abs contact">
    <div class="label">CONTACT US</div>
    <div class="row"><svg width="12" height="9" viewBox="0 0 12 9"><rect width="12" height="9" fill="#222"/><path d="M0 0 L6 5 L12 0" fill="none" stroke="#fff" stroke-width="1"/></svg>info@brenwick-example.com</div>
    <div class="row tel"><svg width="8" height="13" viewBox="0 0 8 13"><rect x=".8" y=".8" width="6.4" height="11.4" rx="1" fill="none" stroke="#222" stroke-width="1.6"/></svg>0147 258 369</div>
  </div>

  <h3 class="abs" style="left:379px;top:1041px">Office Locator</h3>
  <p class="abs small" style="left:381px;top:1074px;width:260px">Lorem ipsum dolor sit amet, consectetur adipiscing elit, sed do eiusmod tempor .....</p>
  <div class="abs zip">Enter Zip Code</div>
  <div class="abs locate">LOCATE</div>

  <h3 class="abs" style="left:683px;top:1041px">Latest News</h3>
  <svg class="abs" style="left:941px;top:1045px" width="26" height="16" viewBox="0 0 26 16"><path d="M9 2 L3 8 L9 14 M17 2 L23 8 L17 14" fill="none" stroke="#222" stroke-width="2"/></svg>
  <div class="abs news-title" style="left:683px;top:1080px">Lorem ipsum dolor sit amet nsectetur</div>
  <p class="abs small" style="left:684px;top:1102px;width:270px">Lorem ipsum dolor sit amet, consectetur adipiscing elit, eiusmod tempor incididunt.....</p>
  <div class="abs readmore" style="left:684px;top:1143px">Read More</div>
</footer>
</body>
</html>
```